Business Card for beauty technology startup

Design Glimora Business Card for a Beauty, based on the website identity and colors (https://www.glimora-example.com).
Glimora is a beauty tech startup that gathers helpful product info for beauty lovers and consumers (such as availability on stores, price range and product reviews) for makeup products. The card design must be young, colorful but clean, and very modern.

Target Market(s)

woman, 15-35

Industry/Entity Type

Cosmetics

Contact Information for Business Card

Full Name, address, phone

Font styles to use
Other font styles liked:
• Advent Pro

Colors
e34297
86cfc6
ffffff
5c5c5c
e8e8e8
e667a6
b2b2b2

Requirements
Must have
• One full colored side with a creative design and another with card info
• Use Color palette: #95C5C5 and/or #D38AA5
• Use fonts: Advent Pro
• Use website identity: https://www.glimora-example.com
Nice to have
• If needed extra font: Roboto

```html
<!DOCTYPE html>
<html lang="en">
<head>
<meta charset="utf-8">
<title>Glimora Business Card</title>
<link rel="stylesheet" href="https://fonts.googleapis.com/css2?family=Advent+Pro:wght@300;400;600&family=Roboto:wght@400;500;700&display=swap">
<style>
  :root {
    --backdrop: #3a3a3d;
    --card: #1f1f23;
    --emboss: #55555b;
    --rose: #b7718e;
    --rose-band: #a96f86;
    --teal: #7fbcbc;
    --white: #ffffff;
  }
  * { margin: 0; padding: 0; box-sizing: border-box; }
  html, body { width: 799px; height: 1200px; overflow: hidden; }
  body {
    background: var(--backdrop);
    display: flex;
    flex-direction: column;
    align-items: center;
    justify-content: center;
    gap: 120px;
    font-family: "Roboto", sans-serif;
  }
  .card {
    position: relative;
    width: 600px;
    height: 343px;
    background: var(--card);
    border-radius: 4px;
    overflow: hidden;
    box-shadow: 0 14px 30px rgba(0,0,0,0.45);
  }
  .card-front {
    display: flex;
    align-items: center;
    justify-content: center;
  }
  .front-wordmark {
    font-family: "Advent Pro", sans-serif;
    font-weight: 400;
    font-size: 64px;
    letter-spacing: 6px;
    color: var(--emboss);
  }
  .back-waves { position: absolute; inset: 0; }
  .brand {
    position: absolute;
    left: 30px;
    top: 26px;
    display: flex;
    align-items: center;
    gap: 16px;
  }
  .brand-dot {
    width: 40px; height: 40px;
    border-radius: 50%;
    border: 2px solid var(--rose);
  }
  .brand-name {
    font-family: "Advent Pro", sans-serif;
    font-weight: 300;
    font-size: 40px;
    letter-spacing: 9px;
    color: var(--rose);
  }
  .holder {
    position: absolute;
    left: 30px;
    top: 92px;
  }
  .holder-name {
    font-weight: 700;
    font-size: 19px;
    letter-spacing: 0.5px;
    color: var(--teal);
    margin-bottom: 8px;
  }
  .holder-address {
    font-size: 13px;
    line-height: 1.35;
    color: var(--rose);
  }
  .contact {
    position: absolute;
    right: 26px;
    bottom: 24px;
    list-style: none;
    text-align: right;
  }
  .contact li {
    display: flex;
    justify-content: flex-end;
    align-items: center;
    gap: 10px;
    font-size: 14px;
    color: var(--white);
    line-height: 22px;
  }
  .contact svg { width: 13px; height: 13px; flex: none; }
</style>
</head>
<body>
  <section class="card card-front">
    <span class="front-wordmark">Glimora</span>
  </section>

  <section class="card card-back">
    <svg class="back-waves" viewBox="0 0 600 343" preserveAspectRatio="none">
      <path d="M0,188 C140,186 290,232 420,232 S560,214 600,196 L600,343 L0,343 Z" fill="var(--rose-band)"/>
      <path d="M0,172 C140,170 290,218 420,218 S560,198 600,180" fill="none" stroke="var(--teal)" stroke-width="8"/>
    </svg>

    <div class="brand">
      <span class="brand-dot"></span>
      <span class="brand-name">GLIMORA</span>
    </div>

    <div class="holder">
      <p class="holder-name">AVA MORGAN</p>
      <p class="holder-address">48, Willow Lane, Fairhaven,<br>Northland - 204517</p>
    </div>

    <ul class="contact">
      <li>00 555 014 720
        <svg viewBox="0 0 16 16"><path d="M4 1 L6 5 L4.5 6.5 C5.5 8.5 7.5 10.5 9.5 11.5 L11 10 L15 12 L13.5 15 C7 14.5 1.5 9 1 2.5 Z" fill="none" stroke="#fff" stroke-width="1.3"/></svg>
      </li>
      <li>www.glimora-example.com
        <svg viewBox="0 0 16 16"><rect x="1" y="6" width="8" height="4" rx="2" fill="none" stroke="#fff" stroke-width="1.3"/><rect x="7" y="6" width="8" height="4" rx="2" fill="none" stroke="#fff" stroke-width="1.3"/></svg>
      </li>
      <li>hello@glimora-example.com
        <svg viewBox="0 0 16 16"><rect x="1" y="3" width="14" height="10" fill="none" stroke="#fff" stroke-width="1.3"/><path d="M1 3 L8 9 L15 3" fill="none" stroke="#fff" stroke-width="1.3"/></svg>
      </li>
    </ul>
  </section>
</body>
</html>
```